wardrobe/costume stylist needs good business card for own business

Hi:)

I'm wanting a business card for my company. I am a freelance stylist.

I do wardrobe/costume stylist to TV commercials; Films; Fashion and Lifestyle shoots.

I'd like a design based around my name Rosalind Parfrey written nicely, maybe a colour? Up to you?!

I've attached a couple of images of business cards I like
.... be creative and have fun!

Thank you :)

Reason: I was trying to get my new business card ready for before I headed overseas Friday morning but I don't think that was realistic so I'd like to extend the deadline to give time to the project. Thank you

Hi designers:) Thank you for all your designs, I've extended the deadline until Sunday, so there's a bit more time. I've attached 3 pictures of business cards which I quite like, please take a look to see if it can be of help in your process. I like the pale plain or patterned background with dark font and the dark plain or patterned background with the pale font the motifs the feminine fonts the plain fonts I like the idea of playing with a circle or some shape on one side of the card with my name or initials as in the picture I have on my post could you play around with this idea a bit please? Thank you all for the work you've done :) Rosa

Hi I am working overseas til Saturday night sorry for no feedback until I teturn Thanks :) Rosa

Hi designers, Thank you all so much for submitting your designs, I really appreciate your input into my project :) I'm sorry I didn't get to respond to some comments, and give feedback. I didn't back from being away until later than I expected, and the deadline had passed then, so apologies. Thanks to you all again for all your really good designs :) Rosa

Target Market(s)

I am a freelance stylist my target audience is producers, production companies, photographers, directors...

Industry/Entity Type

Business

Requirements
Must have
• Rosalind Parfrey
Stylist or Wardrobe Stylist

email rosaparfrey@mailbox-example.co.nz
Mobile 0218467193

(Don't have to use the words 'email' and 'mobile')
Nice to have
• Would like it to be double sided
Like B & W
Like pale colour background with dark font or white font
Like dark colour background with pale font
Should not have
• I would prefer it not to incorporate pictures

```html
<!DOCTYPE html>
<html lang="en">
<head>
<meta charset="UTF-8">
<title>Rosalind Parfrey — Wardrobe Stylist Business Card</title>
<link rel="stylesheet" href="https://fonts.googleapis.com/css2?family=Fondamento&family=Cantarell:wght@400;700&display=swap">
<style>
  :root {
    --canvas: #e9e7e4;
    --card-white: #f6f3f1;
    --card-black: #0b0b0b;
    --accent-red: #b3231c;
    --accent-red-soft: #d9857d;
    --ink-white: #ffffff;
    --rule-grey: #9a9a9a;
    --script: "Fondamento", cursive;
    --sans: "Cantarell", sans-serif;
  }
  * { box-sizing: border-box; margin: 0; padding: 0; }
  html, body {
    width: 1200px;
    height: 900px;
    overflow: hidden;
    background: var(--canvas);
  }
  .sheet {
    width: 1200px;
    height: 900px;
    display: flex;
    flex-direction: column;
    align-items: center;
    justify-content: center;
    gap: 44px;
  }
  .card {
    position: relative;
    width: 700px;
    height: 400px;
    overflow: hidden;
    box-shadow: 0 6px 18px rgba(0,0,0,0.18);
  }

  /* Front: contact side */
  .card--contact { background: var(--card-white); }
  .burst {
    position: absolute;
    inset: 0;
    background: radial-gradient(ellipse 58% 62% at 50% 50%,
      var(--accent-red) 0%,
      var(--accent-red) 18%,
      var(--accent-red-soft) 52%,
      var(--card-white) 100%);
  }
  .contact-block {
    position: absolute;
    left: 300px;
    top: 122px;
    color: var(--ink-white);
  }
  .contact-block .name {
    font-family: var(--script);
    font-size: 38px;
    line-height: 1;
    margin-left: 40px;
  }
  .contact-block .role {
    font-family: var(--sans);
    font-size: 13px;
    letter-spacing: 1px;
    text-transform: uppercase;
    margin: 6px 0 14px 40px;
  }
  .contact-row {
    display: flex;
    align-items: baseline;
    font-family: var(--sans);
    font-size: 17px;
    line-height: 1.8;
  }
  .contact-row .label {
    width: 40px;
    font-weight: 700;
    font-size: 22px;
  }

  /* Back: name side */
  .card--name { background: var(--card-black); }
  .flourish {
    position: absolute;
    left: 0;
    top: 0;
    width: 250px;
    height: 400px;
    background: radial-gradient(ellipse 70% 45% at 20% 50%,
      var(--accent-red) 0%,
      rgba(179,35,28,0.55) 45%,
      rgba(11,11,11,0) 100%);
  }
  .name-block {
    position: absolute;
    left: 300px;
    top: 150px;
    color: var(--ink-white);
    text-align: center;
  }
  .name-block .name {
    font-family: var(--script);
    font-size: 56px;
    line-height: 1;
    padding-bottom: 6px;
  }
  .name-block .role {
    font-family: var(--sans);
    font-size: 19px;
    letter-spacing: 6px;
    text-transform: uppercase;
    padding: 6px 0;
    border-top: 1px solid var(--rule-grey);
    border-bottom: 1px solid var(--rule-grey);
  }
</style>
</head>
<body>
  <main class="sheet">
    <section class="card card--contact">
      <div class="burst" role="img" aria-label="Red radiating burst of fine strands spreading out from the card's centre"></div>
      <div class="contact-block">
        <p class="name">Rosalind Parfrey</p>
        <p class="role">Wardrobe Stylist</p>
        <p class="contact-row"><span class="label">M</span><span>0218467193</span></p>
        <p class="contact-row"><span class="label">E</span><span>rosaparfrey@mailbox-example.co.nz</span></p>
      </div>
    </section>

    <section class="card card--name">
      <div class="flourish" role="img" aria-label="Red swirling floral flourish ornament"></div>
      <div class="name-block">
        <p class="name">Rosalind Parfrey</p>
        <p class="role">Wardrobe Stylist</p>
      </div>
    </section>
  </main>
</body>
</html>
```